Transform Your Giving

I need a tri-fold brochure that will fit in a standard number 10 business envelope. Meadowlark and Allied Services is a charitable nonprofit. The goal of this brochure is to stimulate people into thinking about other ways to make a donation. The design should communicate the essential information on donation options, create a sense of professional integrity, be graphically sharp, easy to read and laid out in a way that doesn't make the material appear crowded.

```html
<!DOCTYPE html>
<html lang="en">
<head>
<meta charset="utf-8">
<title>Transform Your Giving – Tri-fold Brochure</title>
<link href="https://fonts.googleapis.com/css2?family=Montserrat:wght@600;700;800&family=Open+Sans:ital,wght@0,400;0,600;1,400&display=swap" rel="stylesheet">
<style>
:root{
  --navy:#2c2872;
  --navy-deep:#221f5c;
  --green:#7bc142;
  --green-dark:#5ea32c;
  --ink:#3a3a4a;
  --muted:#6b6b7b;
  --white:#ffffff;
  --paper:#f4f4f7;
}
*{box-sizing:border-box;margin:0;padding:0}
html,body{width:720px;height:1200px;overflow:hidden;background:var(--white)}
body{font-family:"Open Sans",Arial,sans-serif;color:var(--ink);position:relative}
.spread{position:absolute;left:12px;width:696px;height:540px;display:flex;box-shadow:0 1px 4px rgba(0,0,0,.18);background:var(--white)}
.spread--outside{top:22px}
.spread--inside{top:616px}
.panel{position:relative;width:232px;height:100%;overflow:hidden}
.photo{position:absolute;left:0;width:100%}
.h-display{font-family:"Montserrat",Arial,sans-serif;font-weight:800;text-transform:uppercase;letter-spacing:.3px}
.body-text{font-size:6.6px;line-height:1.5}
.tab{display:inline-block;font-family:"Montserrat",Arial,sans-serif;font-weight:700;font-size:8.5px;color:var(--white);background:var(--navy);padding:5px 10px;border-right:5px solid var(--green);text-transform:uppercase}
.btn{display:inline-block;background:var(--green);color:var(--white);font-family:"Montserrat",Arial,sans-serif;font-weight:700;font-size:6px;padding:3px 8px;border-radius:2px;text-transform:uppercase}
.brand{display:flex;align-items:center;gap:6px;font-family:"Montserrat",Arial,sans-serif;font-weight:800;color:var(--navy)}
.brand__dot{width:14px;height:14px;border-radius:50%;background:var(--green)}
.brand__sub{font-family:"Montserrat",Arial,sans-serif;font-weight:700;font-size:5.5px;color:var(--navy);text-transform:uppercase;letter-spacing:.4px}
.feature{display:flex;gap:7px;align-items:flex-start;margin-bottom:5px}
.feature__icon{flex:none;width:18px;height:18px;border-radius:50%;background:var(--green)}
.feature__title{font-family:"Montserrat",Arial,sans-serif;font-weight:700;font-size:8px;line-height:1.2}
</style>
</head>
<body>

<!-- OUTSIDE -->
<section class="spread spread--outside">

  <!-- inside flap -->
  <div class="panel" style="background:var(--white)">
    <div class="photo" role="img" aria-label="Photo of grandparents sharing a tender moment with a young grandchild" style="top:0;height:262px;background:linear-gradient(160deg,#d9c2a6,#9c7f66 55%,#6d5a4d)"></div>
    <svg style="position:absolute;left:0;top:236px" width="232" height="40" viewBox="0 0 232 40" aria-hidden="true">
      <path d="M0 14 Q116 40 232 10 L232 40 L0 40Z" fill="var(--white)"/>
      <path d="M0 14 Q116 40 232 10" fill="none" stroke="var(--green)" stroke-width="4"/>
    </svg>
    <div style="position:absolute;top:282px;left:0"><span class="tab">The Impact of Your Gift</span></div>
    <div style="position:absolute;top:314px;left:14px;right:14px">
      <p class="body-text">Your generosity drives our mission. With every thoughtful gift, supporters help families find safety, stability and care in our community. Whether you give today or plan a legacy for tomorrow, each contribution carries forward a promise of protection and hope. Below are simple ways your giving can make a lasting difference.</p>
      <ol class="body-text" style="margin:8px 0 0 12px;font-weight:600;color:var(--navy)">
        <li>Stocks and Securities</li>
        <li>IRA Rollovers</li>
        <li>Bequests</li>
        <li>Life Insurance</li>
        <li>Charitable Annuity</li>
      </ol>
    </div>
    <div style="position:absolute;bottom:0;left:0;width:100%;height:12px;background:var(--navy)"></div>
  </div>

  <!-- back panel -->
  <div class="panel" style="background:var(--white)">
    <div style="position:absolute;top:16px;left:16px;right:16px">
      <p class="body-text">For more than thirty years, Meadowlark and Allied Services has stood beside families in times of need. Your support ensures that every person we serve receives care with dignity, respect and compassion. We thank you for considering a gift.</p>
      <p style="margin-top:12px;font-style:italic;font-size:8px;line-height:1.45;color:var(--navy);font-weight:600;border-left:3px solid var(--green);padding-left:8px">“Giving is not about what we keep, but about what we leave in the lives of others.”</p>
      <p style="margin-top:4px;text-align:right;font-size:6.5px;font-style:italic;color:var(--muted)">— Daniel Harrow</p>
    </div>
    <div style="position:absolute;top:178px;left:0;width:100%;display:flex;flex-direction:column;align-items:center;gap:3px">
      <div class="brand" style="font-size:15px"><span class="brand__dot"></span>Meadowlark</div>
      <div class="brand__sub">Meadowlark and Allied Services</div>
    </div>
    <div style="position:absolute;top:252px;left:0;width:100%;height:288px;background:var(--navy);color:var(--white);padding:22px 18px">
      <h3 class="h-display" style="font-size:11px;text-align:center;margin-bottom:12px">Contact Us</h3>
      <p class="body-text" style="text-align:center;margin-bottom:14px">Have a question about giving? Our planned giving team is glad to help you explore your options.</p>
      <div class="body-text" style="display:flex;flex-direction:column;gap:8px">
        <div style="display:flex;align-items:center;gap:8px"><svg width="11" height="11" viewBox="0 0 24 24"><path fill="var(--green)" d="M6.6 10.8a15 15 0 0 0 6.6 6.6l2.2-2.2c.3-.3.7-.4 1-.2 1.1.4 2.3.6 3.6.6.6 0 1 .4 1 1V20c0 .6-.4 1-1 1A17 17 0 0 1 3 4c0-.6.4-1 1-1h3.5c.6 0 1 .4 1 1 0 1.3.2 2.5.6 3.6.1.3 0 .7-.2 1z"/></svg>(555) 014-2290</div>
        <div style="display:flex;align-items:center;gap:8px"><svg width="11" height="11" viewBox="0 0 24 24"><path fill="var(--green)" d="M2 5h20v14H2z"/><path d="M2 5l10 8 10-8" fill="none" stroke="var(--navy)" stroke-width="2"/></svg>giving@meadowlarkallied.org</div>
        <div style="display:flex;align-items:center;gap:8px"><svg width="11" height="11" viewBox="0 0 24 24"><path fill="var(--green)" d="M12 2a7 7 0 0 0-7 7c0 5 7 13 7 13s7-8 7-13a7 7 0 0 0-7-7zm0 9.5A2.5 2.5 0 1 1 12 6.5a2.5 2.5 0 0 1 0 5z"/></svg>410 Orchard Lane, Fairview, ST 00000</div>
        <div style="display:flex;align-items:center;gap:8px"><svg width="11" height="11" viewBox="0 0 24 24"><circle cx="12" cy="12" r="10" fill="var(--green)"/></svg>www.meadowlarkallied.org</div>
      </div>
      <p style="margin-top:46px;text-align:center;font-family:Montserrat,Arial,sans-serif;font-weight:700;font-size:8px">Follow us:</p>
    </div>
  </div>

  <!-- cover -->
  <div class="panel" style="background:var(--white)">
    <div style="position:absolute;top:0;left:0;width:100%;height:120px;background:var(--navy);padding:22px 14px 0">
      <h1 class="h-display" style="color:var(--white);font-size:15px;line-height:1.1">Transform Your Giving</h1>
      <div style="margin:6px -14px 0;background:var(--green);color:var(--white);padding:4px 14px" class="h-display"><span style="font-size:9.5px">Be Strategic, Be Smart</span></div>
      <p style="margin-top:7px;color:var(--white);font-size:6.6px;line-height:1.45">Discover the impact of Smart Giving with Meadowlark and Allied Services</p>
    </div>
    <div class="photo" role="img" aria-label="Photo of a smiling senior couple walking outdoors together" style="top:120px;height:262px;background:linear-gradient(170deg,#b8c9d9,#8aa7bf 45%,#5f7a63)"></div>
    <svg style="position:absolute;top:130px;left:180px" width="44" height="150" aria-hidden="true">
      <circle cx="22" cy="20" r="14" fill="var(--white)" stroke="var(--green)" stroke-width="2"/>
      <circle cx="22" cy="62" r="14" fill="var(--white)" stroke="var(--green)" stroke-width="2"/>
      <circle cx="22" cy="104" r="14" fill="var(--white)" stroke="var(--green)" stroke-width="2"/>
      <path d="M16 20l4 4 8-8" fill="none" stroke="var(--navy)" stroke-width="2"/>
      <path d="M15 62h14M22 55v14" stroke="var(--navy)" stroke-width="2"/>
      <path d="M22 112s-8-5-8-10a4 4 0 0 1 8-1 4 4 0 0 1 8 1c0 5-8 10-8 10z" fill="var(--navy)"/>
    </svg>
    <svg style="position:absolute;left:0;top:356px" width="232" height="40" viewBox="0 0 232 40" aria-hidden="true">
      <path d="M0 10 Q116 40 232 14 L232 40 L0 40Z" fill="var(--white)"/>
      <path d="M0 10 Q116 40 232 14" fill="none" stroke="var(--green)" stroke-width="4"/>
    </svg>
    <div style="position:absolute;top:420px;left:0;width:100%;display:flex;flex-direction:column;align-items:center;gap:4px">
      <div class="brand" style="font-size:20px"><span class="brand__dot" style="width:18px;height:18px"></span>Meadowlark</div>
      <div class="brand__sub" style="font-size:6.5px">Meadowlark and Allied Services</div>
    </div>
    <div style="position:absolute;bottom:0;left:0;width:100%;height:12px;background:var(--navy)"></div>
  </div>
</section>

<!-- INSIDE -->
<section class="spread spread--inside">

  <div class="panel" style="background:var(--navy);color:var(--white);padding:16px 14px">
    <p class="body-text">We would like to introduce you to Smart Giving. These strategies help you support the causes you care about while also benefiting your own financial plans. Speak with your advisor to learn which fits you best.</p>
    <div style="margin-top:12px" class="feature"><span class="feature__icon"></span><div><div class="feature__title" style="color:var(--green)">Gifts of Stock or Appreciated Securities</div></div></div>
    <p class="body-text">Donating appreciated stock held over a year may let you avoid capital gains tax and receive a deduction for the full market value of the shares.</p>
    <div style="margin:6px 0 12px"><span class="btn">Know more ? Works</span></div>
    <div class="feature"><span class="feature__icon"></span><div class="feature__title" style="color:var(--green)">Donor Advised Fund<br><span style="font-size:6.5px;font-weight:600;color:var(--white)">Strategic &amp; Smart</span></div></div>
    <p class="body-text">A donor advised fund lets you make one contribution, take an immediate deduction and recommend grants to charities over time.</p>
    <div style="margin:6px 0 0"><span class="btn">Know more ? Works</span></div>
    <div class="photo" role="img" aria-label="Photo of a family relaxing together outdoors in a park" style="bottom:0;height:150px;background:linear-gradient(160deg,#9dbb7a,#6f9150 50%,#4d6a3b)"></div>
  </div>

  <div class="panel" style="background:var(--white)">
    <div class="photo" role="img" aria-label="Photo of a senior couple reviewing documents on a tablet at home" style="top:0;height:170px;background:linear-gradient(165deg,#e0d2c0,#b9a48c 50%,#7e6c5c)"></div>
    <div style="position:absolute;top:184px;left:14px;right:14px">
      <div class="feature"><span class="feature__icon"></span><div class="feature__title" style="color:var(--navy)">Qualified Charitable Distributions<br><span style="font-size:6.5px;font-weight:600;color:var(--green-dark)">(QCD) Strategic &amp; Smart</span></div></div>
      <p class="body-text" style="margin-top:4px">If you are 70½ or older, you may transfer funds directly from your IRA to a qualified charity. The gift counts toward your required minimum distribution and is not counted as taxable income.</p>
      <div style="margin:8px 0"><span class="btn">Know more ? Works</span></div>
      <p class="body-text">Many donors choose this option because it is simple, reduces their taxable income and delivers support where it is needed most. Ask your IRA custodian how to begin the transfer.</p>
    </div>
    <div class="photo" role="img" aria-label="Photo of volunteers sharing a meal with community members" style="bottom:0;height:140px;background:linear-gradient(160deg,#c7b596,#8f7d63 55%,#5e5446)"></div>
  </div>

  <div class="panel" style="background:var(--navy);color:var(--white)">
    <div style="padding:16px 14px">
      <div class="feature"><span class="feature__icon"></span><div class="feature__title">Crowdfunding Fundraiser<br><span style="font-size:6.5px;font-weight:600;color:var(--green)">Strategic &amp; Smart</span></div></div>
      <p class="body-text">Invite friends and family to join your giving by creating a personal fundraising page for a birthday, anniversary or memorial.</p>
      <div style="margin:6px 0 12px"><span class="btn">Know more ? Works</span></div>
      <div class="feature"><span class="feature__icon"></span><div class="feature__title">Life Insurance<br><span style="font-size:6.5px;font-weight:600;color:var(--green)">Strategic &amp; Smart</span></div></div>
      <p class="body-text">Name us as a beneficiary of a policy you no longer need, and turn a modest premium into a meaningful future gift.</p>
      <div style="margin:6px 0 12px"><span class="btn">Know more ? Works</span></div>
      <div class="feature"><span class="feature__icon"></span><div class="feature__title">Charitable Gift Annuity<br><span style="font-size:6.5px;font-weight:600;color:var(--green)">Strategic &amp; Smart</span></div></div>
      <p class="body-text">Receive fixed payments for life in exchange for your gift, with the remainder supporting our programs after your lifetime.</p>
      <div style="margin:6px 0 12px"><span class="btn">Know more ? Works</span></div>
      <div class="feature"><span class="feature__icon"></span><div class="feature__title">Bequest<br><span style="font-size:6.5px;font-weight:600;color:var(--green)">Strategic &amp; Smart</span></div></div>
      <p class="body-text">Include a gift in your will or trust to leave a legacy of care for generations to come.</p>
    </div>
    <div style="position:absolute;bottom:0;left:0;width:100%;height:34px;background:var(--white);display:flex;align-items:center;justify-content:center;font-family:Montserrat,Arial,sans-serif;font-weight:700;font-size:9px;color:var(--navy)">www.meadowlarkallied.org</div>
  </div>
</section>

</body>
</html>
```